Luxury Business Card Design for High-End Window Treatments

Gilded Slatworks
Custom Plantation Shutters & Architectural Shading Systems

⸻

BACK

Daniel Trevick
Owner

Custom Interior & Exterior Window Treatments

919-555-0148
gildedslatworks.com

I have included a picture that I’m hoping we can use on the back, but I’m also wondering if you can get rid of the ladder? Should we get rid of shutters , shades and blinds underneath Gilded Slatworks?

Target Market(s)

High-end residential homeowners, custom home builders, architects, interior designers, and luxury renovation clients seeking premium plantation shutters and motorized architectural shading systems.

Industry/Entity Type

Custom Window treatments

Contact Information for Business Card

Front Gilded Slatworks Custom Plantation Shutters Motorized Architectural Shading Systems BACK Daniel Trevick Owner 919-555-0148 GildedSlatworks.com Custom Interior & Exterior Window Treatments By Appointment

Requirements
Nice to have
• Not 100% sure on nice to halves or the color but you can definitely check out my website to get a better understanding of what I’m trying to do

```html
<!DOCTYPE html>
<html lang="en">
<head>
<meta charset="utf-8">
<title>Gilded Slatworks – Business Card</title>
<link rel="stylesheet" href="https://fonts.googleapis.com/css2?family=Marcellus&family=Poppins:wght@400&display=swap">
<style>
  :root {
    --backdrop: #9a9a9a;
    --card-black: #000000;
    --gold: #c2ab4f;
    --photo-light: #6c7a84;
    --photo-dark: #383c3a;
    --white: #ffffff;
  }
  * { margin: 0; padding: 0; box-sizing: border-box; }
  html, body {
    width: 1093px; height: 1200px; overflow: hidden;
    background: var(--backdrop);
  }
  .card {
    position: absolute;
    left: 264px;
    width: 580px;
    height: 358px;
    background: var(--card-black);
    overflow: hidden;
    color: var(--white);
    font-family: "Poppins", sans-serif;
  }
  .card--contact { top: 226px; }
  .card--brand { top: 620px; }

  .gold-band {
    position: absolute; top: 0; right: 0; bottom: 0; width: 176px;
    background: var(--gold);
  }
  .black-fade {
    position: absolute; top: 0; left: 0; bottom: 0; width: 404px;
    background: linear-gradient(90deg, #000 62%, #161616 100%);
  }
  .hex-frame { position: absolute; left: 0; top: 0; }

  .holder { position: absolute; left: 27px; top: 40px; }
  .holder__name {
    font-family: "Marcellus", serif;
    font-weight: 400;
    font-size: 25px; line-height: 1; color: var(--gold);
  }
  .holder__role { font-size: 17px; line-height: 1.1; margin-top: 1px; }

  .services {
    position: absolute; left: 27px; top: 171px;
    font-size: 17.3px; line-height: 21px;
  }
  .contact {
    position: absolute; left: 27px; top: 282px;
    list-style: none; font-size: 17px; line-height: 22px;
  }
  .contact__item { display: flex; align-items: center; gap: 8px; }
  .contact__icon { width: 16px; height: 16px; flex: none; }

  .brand-name {
    position: absolute; left: 0; right: 0; top: 98px;
    text-align: center;
    font-family: "Poppins", sans-serif;
    font-weight: 400;
    font-size: 50px; line-height: 62px;
    color: var(--gold);
  }
  .tagline {
    position: absolute; left: 0; right: 0; top: 279px;
    text-align: center; font-size: 16.5px; line-height: 21px;
  }
  .tagline__divider { color: var(--gold); }
</style>
</head>
<body>
  <section class="card card--contact">
    <div class="black-fade"></div>
    <div class="gold-band"></div>
    <svg class="hex-frame" width="580" height="358" viewBox="0 0 580 358">
      <defs>
        <linearGradient id="photoTone" x1="0" y1="0" x2="1" y2="1">
          <stop offset="0" stop-color="var(--photo-light)"/>
          <stop offset="1" stop-color="var(--photo-dark)"/>
        </linearGradient>
      </defs>
      <polygon points="199,176 293,11 483,11 579,176 483,341 293,341" fill="var(--gold)"/>
      <polygon role="img" aria-label="Photo of a two-storey porch fitted with dark exterior roller shades"
               points="209,176 299,19 479,19 569,176 479,332 299,332" fill="url(#photoTone)"/>
    </svg>

    <div class="holder">
      <h1 class="holder__name">Daniel Trevick</h1>
      <p class="holder__role">Owner</p>
    </div>

    <p class="services">Custom Interior &amp;<br>Exterior Window<br>Treatments<br>By Appointment</p>

    <ul class="contact">
      <li class="contact__item">
        <svg class="contact__icon" viewBox="0 0 24 24" fill="none" stroke="var(--gold)" stroke-width="2.2" stroke-linecap="round">
          <path d="M5 3l4 1 1 4-2 2c1 3 3 5 6 6l2-2 4 1 1 4-2 2C10 21 3 14 3 5z" fill="var(--gold)" stroke="none"/>
          <path d="M14 3a7 7 0 0 1 7 7M14 7a3 3 0 0 1 3 3"/>
        </svg>
        <span>919-555-0148</span>
      </li>
      <li class="contact__item">
        <svg class="contact__icon" viewBox="0 0 24 24">
          <rect x="1" y="5" width="22" height="14" fill="var(--gold)"/>
          <path d="M1 5l11 8 11-8" fill="none" stroke="#000" stroke-width="1.5"/>
        </svg>
        <span>GildedSlatworks.com</span>
      </li>
    </ul>
  </section>

  <section class="card card--brand">
    <p class="brand-name">Gilded<br>Slatworks</p>
    <p class="tagline">Gilded Slatworks Custom <span class="tagline__divider">|</span> Plantation Shutters Motorized<br>Architectural Shading Systems</p>
  </section>
</body>
</html>
```